ORLA - Óptica Médica - web design and concept

Website concept - Create and develop our website design and structure. ORLA is an optical store chain, and we are looking to establish our web and digital concept. In attachment there are several pictures about our stores and our logo.

The website structure should be user friendly. Colors should be light and the design as simple and minimalist as possible. There are different variations of the logothat can be used, check the file.

The website will include optical collections and sun collections as an online store. Also, a medical menu should be considered in order for clients to schedule optometry appointments. There should also be a menu for client assistance where the clients can read about glass maintenance in our workshop.
Updates

Low design quality

Number of Pages Required

5+ page

Font styles to use
Serif
Sans Serif

Requirements
Must have
• Must be user-friendly and minimalist.
• Please USE PICTURES FROM THE BRANDS we sell: MERUN, BOSKA, PNW, KOLE, BAMPE
Nice to have
• Nice to inspire: ZEK glasses (see website https://ch.shopzek.com/en/)
• Nice to inspire: https://merun-eyewear.com/
• Nice to ispire: https://www.pnwglobe.com/en/
Should not have
• Hysteric colors and shapes

```html
<!DOCTYPE html>
<html lang="en">
<head>
<meta charset="utf-8">
<title>ORLA Óptica – Eye Wear</title>
<link href="https://fonts.googleapis.com/css2?family=Poppins:wght@300;400;500;600;700&display=swap" rel="stylesheet">
<style>
:root{
  --gold:#c9923f;
  --gold-soft:#d7a65a;
  --black:#0d0d0d;
  --ink:#222;
  --muted:#555;
  --white:#fff;
  --paper:#f6f6f6;
}
*{margin:0;padding:0;box-sizing:border-box}
html,body{width:1200px;height:4027px;overflow:hidden}
body{position:relative;font-family:'Poppins',sans-serif;color:var(--ink);background:var(--white)}
.abs{position:absolute}
/* header */
.site-header{position:absolute;left:0;top:0;width:1200px;height:120px;background:var(--black);z-index:5}
.brand-badge{position:absolute;left:118px;top:0;width:140px;height:160px;background:var(--black);border-radius:0 0 70px 70px;z-index:6;display:flex;align-items:center;justify-content:center}
.brand-name{font-family:'Poppins',sans-serif;font-weight:500;color:var(--gold);font-size:34px;letter-spacing:4px}
.call{position:absolute;left:562px;top:24px;display:flex;align-items:center;gap:12px;color:var(--white);font-size:19px;font-weight:500}
.call-icon{width:30px;height:30px;border-radius:50%;border:2px solid var(--gold);display:flex;align-items:center;justify-content:center}
.search{position:absolute;left:813px;top:26px;width:202px;height:28px;background:var(--white);border-radius:14px;font-size:11px;color:#888;padding:7px 14px}
.search svg{position:absolute;right:10px;top:7px}
.search-btn{position:absolute;left:1038px;top:26px;width:28px;height:28px;border-radius:50%;background:var(--gold)}
.main-nav{position:absolute;left:476px;top:78px;display:flex;gap:0;font-size:14.5px;font-weight:500;color:var(--white)}
.main-nav span{margin-right:30px}
/* hero */
.hero{position:absolute;left:0;top:120px;width:1200px;height:600px;background:linear-gradient(100deg,#2b2520 0%,#5a4a3f 35%,#8b7866 60%,#c9bfb3 100%)}
.hero-text{position:absolute;left:129px;top:290px;color:var(--white)}
.hero-kicker{font-size:38px;font-weight:300;letter-spacing:1px}
.hero-title{font-size:64px;font-weight:700;letter-spacing:3px;line-height:1.05}
.btn-gold{display:inline-block;background:var(--gold);color:var(--white);font-size:15px;font-weight:600;padding:12px 28px;border-radius:24px;margin-top:22px}
.hero-arrow{position:absolute;top:352px;width:34px;height:34px;border-radius:50%;background:rgba(0,0,0,.55);display:flex;align-items:center;justify-content:center}
.hero-curve{position:absolute;left:0;top:590px;width:1200px;height:140px}
/* guarantees */
.section-title{position:absolute;left:0;width:1200px;text-align:center;font-size:30px;font-weight:400;letter-spacing:1px}
.section-title b{color:var(--gold);font-weight:600}
.guarantee{position:absolute;top:872px;width:240px;text-align:center}
.g-icon{width:98px;height:98px;margin:0 auto;border-radius:50%;border:5px solid var(--gold);display:flex;align-items:center;justify-content:center}
.guarantee h3{font-size:18px;font-weight:500;margin-top:32px;color:var(--ink)}
.guarantee p{font-size:12.5px;line-height:22px;color:var(--muted);margin-top:10px}
/* welcome */
.welcome-photo{position:absolute;left:0;top:1195px;width:600px;height:510px;background:linear-gradient(180deg,#1d1b18 0%,#2f4a47 45%,#8d7a5a 75%,#c9c0ae 100%)}
.welcome-panel{position:absolute;left:540px;top:1195px;width:660px;height:510px}
.welcome-copy{position:absolute;left:668px;top:1290px;width:480px;color:var(--white)}
.welcome-copy h2{font-size:30px;font-weight:600;line-height:1.2}
.welcome-copy h2 span{display:block;font-size:46px;font-weight:700}
.welcome-copy p{font-size:12.5px;line-height:24px;margin-top:22px}
.btn-outline{display:inline-block;border:2px solid var(--white);color:var(--white);font-size:13px;font-weight:500;padding:8px 22px;border-radius:22px;margin-top:26px}
/* products */
.intro{position:absolute;left:200px;top:1855px;width:800px;text-align:center;font-size:13.5px;line-height:26px;color:var(--muted)}
.card{position:absolute;width:296px;height:312px;border-radius:6px;overflow:hidden}
.card-box{position:absolute;left:28px;right:28px;top:183px;height:80px;background:rgba(255,255,255,.92);border-radius:4px;text-align:center;padding:12px 14px}
.card-box h4{font-size:15px;font-weight:400;letter-spacing:.5px}
.card-box h4 b{font-weight:700}
.card-box p{font-size:11.5px;line-height:18px;color:var(--muted);margin-top:6px}
/* blog */
.blog{position:absolute;left:0;top:2744px;width:1200px;height:526px;background:radial-gradient(ellipse at 55% 35%,#dca964 0%,var(--gold) 55%,#b88233 100%)}
.blog-card{position:absolute;top:2913px;width:296px;height:304px;border-radius:6px;overflow:hidden}
.blog-box{position:absolute;left:24px;right:24px;top:148px;height:94px;background:rgba(255,255,255,.93);border-radius:4px;text-align:center;padding:14px 12px;font-size:15px;line-height:22px;color:var(--ink)}
.blog-date{display:flex;justify-content:center;align-items:center;gap:8px;font-size:13px;margin-top:6px}
/* brands */
.brands{position:absolute;left:0;top:3330px;width:1200px;height:80px}
.brand{position:absolute;top:24px;font-size:20px;font-weight:600;color:var(--black);letter-spacing:1px}
/* footer */
.footer-shape{position:absolute;left:0;top:3470px;width:1200px;height:120px}
.footer{position:absolute;left:0;top:3570px;width:1200px;height:457px;background:var(--black);color:var(--white)}
.f-title{position:absolute;top:95px;font-size:22px;font-weight:600}
.f-title span{color:var(--gold)}
.f-links{position:absolute;left:131px;top:150px;font-size:13px;line-height:24.5px}
.f-links li{list-style:none;padding-left:20px;position:relative}
.f-links li:before{content:"›";position:absolute;left:0;color:var(--white)}
.f-contact{position:absolute;left:349px;font-size:12.5px;line-height:19px;display:flex;gap:14px}
.f-signup{position:absolute;left:617px;top:130px;width:320px;font-size:11.5px;line-height:19px;color:#ccc}
.f-input{position:absolute;left:617px;top:193px;width:310px;height:34px;background:var(--white);border-radius:17px;font-size:11px;color:#777;padding:10px 16px}
.f-sub{position:absolute;left:820px;top:193px;width:108px;height:34px;background:var(--gold);border-radius:17px;font-size:12px;font-weight:600;color:var(--white);text-align:center;line-height:34px}
.f-social{position:absolute;left:617px;top:254px;display:flex;gap:8px}
.f-social i{width:26px;height:26px;border-radius:50%;border:1.5px solid var(--white);display:block}
.f-brand{position:absolute;left:985px;top:120px;width:120px;text-align:center}
.copyright{position:absolute;left:0;top:398px;width:1200px;text-align:center;font-size:12.5px;color:#ddd}
</style>
</head>
<body>

<header class="site-header">
  <div class="call">
    <span class="call-icon"><svg width="14" height="14" viewBox="0 0 24 24"><path fill="#c9923f" d="M6.6 10.8a15 15 0 0 0 6.6 6.6l2.2-2.2c.3-.3.7-.4 1-.2 1.1.4 2.3.6 3.6.6.6 0 1 .4 1 1V20c0 .6-.4 1-1 1A17 17 0 0 1 3 4c0-.6.4-1 1-1h3.5c.6 0 1 .4 1 1 0 1.2.2 2.4.6 3.6.1.3 0 .7-.2 1z"/></svg></span>
    Call Us 900 11 22 33
  </div>
  <div class="search">Search
    <svg width="13" height="13" viewBox="0 0 24 24"><circle cx="10" cy="10" r="7" fill="none" stroke="#333" stroke-width="3"/><path d="M15 15l6 6" stroke="#333" stroke-width="3"/></svg>
  </div>
  <div class="search-btn"></div>
  <nav class="main-nav">
    <span>HOME</span><span>ABOUT US</span><span>PRODUCTS</span><span>CONTACT US</span><span>BLOG</span><span>ONLINE STORE</span>
  </nav>
</header>
<div class="brand-badge"><span class="brand-name">ORLA</span></div>

<section class="hero" role="img" aria-label="Photo of a smiling woman adjusting black eyeglasses inside an optical store with frames on display shelves"></section>
<div class="hero-text">
  <div class="hero-kicker">ORLA ÓPTICA</div>
  <div class="hero-title">EYE WEAR</div>
  <span class="btn-gold">SCHEDULE APPOINTMENT</span>
</div>
<div class="hero-arrow" style="left:66px"><svg width="12" height="12" viewBox="0 0 12 12"><path d="M8 1L3 6l5 5" fill="none" stroke="#fff" stroke-width="2"/></svg></div>
<div class="hero-arrow" style="left:1096px"><svg width="12" height="12" viewBox="0 0 12 12"><path d="M4 1l5 5-5 5" fill="none" stroke="#fff" stroke-width="2"/></svg></div>
<svg class="hero-curve" viewBox="0 0 1200 140" preserveAspectRatio="none">
  <path d="M0 20 C300 70 520 120 620 120 C760 120 980 60 1200 10 L1200 140 L0 140 Z" fill="#fff"/>
</svg>

<h2 class="section-title" style="top:778px"><b>OUR</b> GUARANTEES</h2>

<div class="guarantee" style="left:114px">
  <div class="g-icon"><svg width="40" height="40" viewBox="0 0 40 40" fill="#c9923f"><circle cx="20" cy="7" r="5"/><path d="M6 14l3-3 8 5h6l8-5 3 3-9 6v16h-5v-9h-2v9h-5V20z"/></svg></div>
  <h3>Orla Childhood</h3>
  <p>50% discount on new glasses, if your child's graduation has changed before six months.</p>
</div>
<div class="guarantee" style="left:358px">
  <div class="g-icon"><svg width="44" height="40" viewBox="0 0 44 40" fill="#c9923f"><rect x="3" y="10" width="24" height="18" rx="2"/><path d="M27 15h8l6 7v6H27z"/><circle cx="11" cy="31" r="4"/><circle cx="34" cy="31" r="4"/></svg></div>
  <h3>Orla Accident Warranty</h3>
  <p>Did you get off your glasses when you got out of the car? Did your little boy play with his sunglasses?</p>
</div>
<div class="guarantee" style="left:594px">
  <div class="g-icon"><svg width="36" height="40" viewBox="0 0 36 40"><path d="M10 18V11a8 8 0 0 1 16 0" fill="none" stroke="#c9923f" stroke-width="4"/><rect x="5" y="18" width="26" height="20" rx="3" fill="#c9923f"/><circle cx="18" cy="27" r="3" fill="#fff"/></svg></div>
  <h3>Orla Security</h3>
  <p>If you have suffered a robbery or robbery in your home, you will opt for the replacement of the same product at half price.</p>
</div>
<div class="guarantee" style="left:852px">
  <div class="g-icon"><svg width="44" height="30" viewBox="0 0 44 30"><path d="M2 15C9 4 35 4 42 15 35 26 9 26 2 15z" fill="none" stroke="#c9923f" stroke-width="3.5"/><circle cx="22" cy="15" r="7" fill="#c9923f"/></svg></div>
  <h3>Orla Vision</h3>
  <p>If you suffer from a diagnosed visual pathology and during the first two years your graduation changes, we replenish your crystals to 50%.</p>
</div>

<div class="welcome-photo" role="img" aria-label="Interior of an elegant optical store with teal display walls, gold lighting and a central counter"></div>
<svg class="welcome-panel" viewBox="0 0 660 510" preserveAspectRatio="none"><polygon points="20,0 660,0 660,510 0,510" fill="#c9923f"/></svg>
<div class="welcome-copy">
  <h2>WELCOME TO<span>ORLA OPTICA</span></h2>
  <p>Sed ut perspiciatis unde omnis iste natus error sit voluptatem accusantium doloremque laudantium, totam rem aperiam, eaque ipsa quae ab illo inventore veritatis et quasi architecto beatae vitae dicta sunt explicabo. Nemo enim ipsam voluptatem quia voluptas sit aspernatur aut odit aut fugit, sed quia consequuntur magni dolores eos qui ratione voluptatem sequi nesciunt. Neque porro quisquam est, qui dolorem ipsum quia dolor sit amet, consectetur, adipisci velit</p>
  <span class="btn-outline">READ MORE</span>
</div>

<h2 class="section-title" style="top:1800px"><b>OUR</b> PRODUCTS</h2>
<p class="intro">At Orla Optica we offer you personalized attention. Our professional experience, together with our products of the highest quality, make the difference that makes us unique in Ribera.</p>

<div class="card" style="left:134px;top:1957px;background:linear-gradient(135deg,#5a3a2c,#b88d73 60%,#e5d6c8)" role="img" aria-label="Woman wearing black graduated eyeglass frames">
  <div class="card-box"><h4><b>GRADUATED</b> FRAME</h4><p>We have a selection of frames from the best brands: Jenna Colt</p></div>
</div>
<div class="card" style="left:451px;top:1957px;background:linear-gradient(135deg,#f1c7c3,#e9a9a3 50%,#fbe8e4)" role="img" aria-label="Young girl wearing red children's glasses">
  <div class="card-box"><h4><b>SPECIAL</b> CHILDREN</h4><p>Did you know that a high percentage of children suffer from some</p></div>
</div>
<div class="card" style="left:771px;top:1957px;background:linear-gradient(160deg,#e8f4fa,#9fd0e6 55%,#5aa6c8)" role="img" aria-label="Close-up of transparent contact lenses on a blue background">
  <div class="card-box"><h4><b>OPHTHALMIC</b> LENSES</h4><p>We guarantee our clients a personalized attention, advising them</p></div>
</div>
<div class="card" style="left:134px;top:2285px;background:linear-gradient(135deg,#e2a94d,#9a6a3a 50%,#3e6f85)" role="img" aria-label="Two friends wearing colourful sunglasses and hats">
  <div class="card-box"><h4><b>SUN</b> GLASSES</h4><p>Protect yourself adequately from ultraviolet (UV) rays thanks</p></div>
</div>
<div class="card" style="left:451px;top:2285px;background:linear-gradient(180deg,#dde9f3,#a7c6e0 60%,#7aa4c9)" role="img" aria-label="Contact lens held on a fingertip">
  <div class="card-box"><h4><b>CONTACT</b> LENSES</h4><p>As experts in the adaptation of contact lenses</p></div>
</div>
<div class="card" style="left:771px;top:2285px;background:linear-gradient(135deg,#cfd6dc,#8d9aa5 50%,#c8a06c)" role="img" aria-label="Older man looking through a magnifying glass">
  <div class="card-box"><h4><b>LOW</b> VISION</h4><p>We have a selection of frames from the best brands: Jenna Colt</p></div>
</div>

<section class="blog" role="img" aria-label="Warm gold background with a soft close-up of an eye"></section>
<h2 class="section-title" style="top:2818px;color:#fff">LATEST <b style="color:#fff">BLOG</b></h2>

<div class="blog-card" style="left:134px;background:linear-gradient(135deg,#2e7d86,#c65b4e 60%,#e7b9a0)" role="img" aria-label="Woman in red glasses against a teal wall">
  <div class="blog-box">Sed ut perspiciatis unde omnis iste natus
    <div class="blog-date"><svg width="12" height="12" viewBox="0 0 12 12"><rect x="1" y="2" width="10" height="9" fill="none" stroke="#333" stroke-width="1.5"/><path d="M1 5h10" stroke="#333" stroke-width="1.5"/></svg>Oct 01, 2018</div>
  </div>
</div>
<div class="blog-card" style="left:451px;background:linear-gradient(180deg,#2a2622,#5c4d3a 50%,#cbbfa8)" role="img" aria-label="Optical store interior with display counters">
  <div class="blog-box">Sed ut perspiciatis unde omnis iste natus
    <div class="blog-date"><svg width="12" height="12" viewBox="0 0 12 12"><rect x="1" y="2" width="10" height="9" fill="none" stroke="#333" stroke-width="1.5"/><path d="M1 5h10" stroke="#333" stroke-width="1.5"/></svg>Oct 01, 2018</div>
  </div>
</div>
<div class="blog-card" style="left:771px;background:linear-gradient(135deg,#f3c9c2,#e49a91 55%,#fae4dd)" role="img" aria-label="Girl wearing red glasses smiling">
  <div class="blog-box">Sed ut perspiciatis unde omnis iste natus
    <div class="blog-date"><svg width="12" height="12" viewBox="0 0 12 12"><rect x="1" y="2" width="10" height="9" fill="none" stroke="#333" stroke-width="1.5"/><path d="M1 5h10" stroke="#333" stroke-width="1.5"/></svg>Oct 01, 2018</div>
  </div>
</div>

<div class="brands">
  <span class="brand" style="left:232px">VARDEN</span>
  <span class="brand" style="left:405px;font-weight:400">JENNA COLT</span>
  <span class="brand" style="left:592px">LUMIO</span>
  <span class="brand" style="left:752px;font-weight:400">CASA HELVIA</span>
  <span class="brand" style="left:920px">CORSIVA</span>
</div>

<svg class="footer-shape" viewBox="0 0 1200 120" preserveAspectRatio="none">
  <polygon points="0,0 560,70 1200,50 1200,120 0,120" fill="#0d0d0d"/>
  <polygon points="0,0 560,70 0,100" fill="#c9923f"/>
</svg>
<footer class="footer">
  <div class="f-title" style="left:131px">Quick <span>Links</span></div>
  <ul class="f-links">
    <li>Home</li><li>About Us</li><li>Products</li><li>Contact</li><li>Blog</li><li>Store</li>
  </ul>

  <div class="f-title" style="left:349px">Contact <span>Us</span></div>
  <div class="f-contact" style="top:150px">
    <svg width="14" height="18" viewBox="0 0 14 18"><path d="M7 0a7 7 0 0 1 7 7c0 5-7 11-7 11S0 12 0 7a7 7 0 0 1 7-7z" fill="#fff"/><circle cx="7" cy="7" r="2.5" fill="#0d0d0d"/></svg>
    <div>Orla Optica<br>Address<br>Calle Olmo, 12. Ribera</div>
  </div>
  <div class="f-contact" style="top:222px">
    <svg width="14" height="14" viewBox="0 0 24 24"><path fill="#fff" d="M6.6 10.8a15 15 0 0 0 6.6 6.6l2.2-2.2c.3-.3.7-.4 1-.2 1.1.4 2.3.6 3.6.6.6 0 1 .4 1 1V20c0 .6-.4 1-1 1A17 17 0 0 1 3 4c0-.6.4-1 1-1h3.5c.6 0 1 .4 1 1 0 1.2.2 2.4.6 3.6.1.3 0 .7-.2 1z"/></svg>
    <div>Phone : 700 555 0142</div>
  </div>
  <div class="f-contact" style="top:260px">
    <svg width="15" height="12" viewBox="0 0 15 12"><rect width="15" height="12" rx="1" fill="#fff"/><path d="M0 1l7.5 6L15 1" fill="none" stroke="#0d0d0d" stroke-width="1.5"/></svg>
    <div>Email : info@orlaoptica.com</div>
  </div>

  <div class="f-title" style="left:617px;font-size:19px">SIGN UP TO RECEIVE <span>EMAIL</span></div>
  <p class="f-signup">Excepteur sint occaecat cupidatat non proident, sunt in culpa qui Nemo enim ipsam voluptatem</p>
  <div class="f-input">Enter Email</div>
  <div class="f-sub">SUBSCRIBE</div>
  <div class="f-social"><i></i><i></i><i></i><i></i></div>

  <div class="f-brand"><span class="brand-name">ORLA</span></div>

  <p class="copyright">© Copyright 2018 ORLA Optica All rights reserved</p>
</footer>

</body>
</html>
```